Flat bootstrap design for existing site

I'm looking for a modern flat design based around an existing logo. This has to be a custom design (no external templates), and implemented into a bootstrap framework.

The logo is attached as 2 versions - choose whichever you want, that flows better with whatever design you choose.

Added screenshots of the existing site (currently using the default bootstrap layouts). Please make your designs around those pages in the screenshots (i.e. the homepage only has the postal code input and the header). The active page has 3 screenshots, because I wanted to illustrate the other states that would be visible (in the table rows).

This is a moving/junk removal website, just for some context.

Here's some example websites (flat designs) that I like, just to give you an idea of what I'm after.

https://www.plimvora.com/
https://dacklow.com/
https://trevanu.com/
https://quobrintal.com/en/

Coding

Coded - Design and coding required

Number of Pages Required

5+ page

Colors

Designer to choose colors to be used in the design.

Requirements
Must have
• It must be a modern/simple flat design, that is built around the existing logo (attached).
• It has to be implemented using bootstrap.

```html
<!DOCTYPE html>
<html lang="en">
<head>
<meta charset="utf-8">
<title>Haulvo – Booking Details</title>
<link href="https://fonts.googleapis.com/css2?family=Open+Sans:wght@400;600;700&display=swap" rel="stylesheet">
<style>
:root{
  --sky:#4bc8f4;
  --navy:#2566a0;
  --ink:#333;
  --text:#555;
  --line:#e3e3e3;
  --page:#f7f7f7;
  --white:#fff;
  --green:#5cb85c;
  --dark:#3a3a3a;
  --addon:#d0d0d0;
}
*{box-sizing:border-box;margin:0;padding:0}
html,body{width:1200px;height:902px;overflow:hidden}
body{font-family:"Open Sans",sans-serif;background:var(--page);color:var(--ink);position:relative}
.site-header{position:absolute;left:0;top:0;width:1200px;height:88px;background:var(--white);border-top:3px solid var(--sky);border-bottom:1px solid var(--line)}
.brand{position:absolute;left:132px;top:20px;display:flex;align-items:center;gap:8px;font-size:34px;font-weight:700;color:var(--sky);letter-spacing:1px}
.brand-dot{width:14px;height:14px;border-radius:50%;background:var(--sky)}
.main-nav{position:absolute;left:0;top:0;height:85px}
.main-nav a{position:absolute;top:0;height:85px;line-height:85px;font-size:13.5px;color:var(--ink);text-decoration:none;text-align:center;white-space:nowrap}
.nav-book{left:470px;width:84px}
.nav-how{left:585px;width:130px}
.nav-driver{left:737px;width:173px;background:var(--sky);color:var(--white)!important}
.nav-user{left:935px;width:140px;text-align:left!important}
.caret{display:inline-block;margin-left:7px;border-left:4px solid transparent;border-right:4px solid transparent;border-top:5px solid var(--ink);vertical-align:middle}
.panel{position:absolute;left:132px;top:121px;width:936px;height:331px;background:var(--white);border:1px solid var(--line)}
.panel-head{height:51px;background:var(--sky);color:var(--white);font-size:16px;line-height:51px;padding-left:26px;letter-spacing:.3px}
.field-label{position:absolute;font-size:13.5px;font-weight:600;color:var(--ink);line-height:18px}
.input{position:absolute;height:39px;border:1px solid #dcdcdc;font-size:12px;color:var(--text);padding:0 11px;line-height:37px;background:var(--white)}
.select-arrows{position:absolute;right:10px;top:14px}
.addon{position:absolute;right:0;top:0;width:42px;height:37px;background:var(--addon);display:flex;align-items:center;justify-content:center}
.btn-update{position:absolute;left:26px;top:264px;width:87px;height:38px;background:var(--sky);color:var(--white);font-size:13.5px;font-weight:600;line-height:38px;text-align:center}
.divider{position:absolute;left:132px;top:475px;width:936px;border-top:1px solid #eaeaea}
.section-title{position:absolute;left:132px;top:494px;font-size:24px;font-weight:400;color:var(--ink)}
.notice{position:absolute;left:132px;top:543px;width:936px;height:51px;background:var(--navy);color:var(--white);font-size:13px;font-weight:600;line-height:51px;padding-left:26px}
.drivers{position:absolute;left:132px;top:594px;width:936px;border-collapse:collapse;background:var(--white);font-size:12px;color:var(--text);table-layout:fixed}
.drivers th,.drivers td{border:1px solid var(--line);text-align:left;vertical-align:middle;white-space:nowrap}
.drivers th{height:48px;font-size:13px;font-weight:600;color:var(--ink)}
.drivers td{height:40px}
.drivers .c-name{padding-left:26px}
.drivers th.c-name{padding-left:27px}
.drivers .c-dist,.drivers .c-time{padding-left:15px}
.drivers th.c-dist,.drivers th.c-time{padding-left:16px}
.drivers .c-status{padding-left:14px}
.drivers .c-pay{padding-left:28px}
.badge{display:inline-block;width:93px;height:24px;line-height:24px;text-align:center;font-size:10.5px;font-weight:700;color:var(--white);border-radius:2px}
.badge-accepted{background:var(--green)}
.badge-sent{background:var(--sky)}
.badge-pending{background:var(--dark);width:69px}
.paid{font-weight:700;color:var(--ink);font-size:12px}
.site-footer{position:absolute;left:0;top:846px;width:1200px;height:56px;background:var(--white);border-top:1px solid var(--line);font-size:11.5px;color:var(--text)}
.site-footer p{position:absolute;top:0;left:0;width:1200px;text-align:center;line-height:56px}
.site-footer .code{position:absolute;left:1098px;top:0;line-height:56px}
</style>
</head>
<body>
<header class="site-header">
  <div class="brand"><span class="brand-dot"></span>HAULVO</div>
  <nav class="main-nav">
    <a class="nav-book">BOOK</a>
    <a class="nav-how">HOW IT WORKS</a>
    <a class="nav-driver">BECOME A DRIVER</a>
    <a class="nav-user">George@mailbrook.com<span class="caret"></span></a>
  </nav>
</header>

<section class="panel">
  <div class="panel-head">BOOKING DETAILS</div>
  <div class="field-label" style="left:27px;top:70px">Package Selected :</div>
  <div class="field-label" style="left:479px;top:70px">Pick - up Time Selected :</div>
  <div class="input" style="left:26px;top:97px;width:429px">Package 1
    <svg class="select-arrows" width="7" height="10" viewBox="0 0 7 10"><path d="M3.5 0L7 4H0z M3.5 10L0 6h7z" fill="#555"/></svg>
  </div>
  <div class="input" style="left:478px;top:97px;width:429px">July 18 at 4:13 am
    <span class="addon"><svg width="11" height="11" viewBox="0 0 11 11"><rect x=".5" y="1.5" width="10" height="9" fill="none" stroke="#fff"/><path d="M.5 4h10M3 1v2M8 1v2M3 6h1M5 6h1M7 6h1M3 8h1M5 8h1M7 8h1" stroke="#fff"/></svg></span>
  </div>
  <div class="field-label" style="left:27px;top:150px">Description</div>
  <div class="input" style="left:26px;top:177px;width:881px;height:71px;line-height:1;padding-top:13px">1 Large Stove</div>
  <div class="btn-update">UPDATE</div>
</section>

<div class="divider"></div>
<h2 class="section-title">Drivers In Your Area</h2>
<div class="notice">Please Stay on this page and be patient,while we contact the drivers and find you one ASAP</div>

<table class="drivers">
  <colgroup><col style="width:204px"><col style="width:175px"><col style="width:176px"><col style="width:176px"><col style="width:205px"></colgroup>
  <thead><tr><th class="c-name">Name</th><th class="c-dist">Distance (km)</th><th class="c-time">Agreed Pick-up time</th><th class="c-status"></th><th class="c-pay"></th></tr></thead>
  <tbody>
    <tr><td class="c-name">Larry Dunmore</td><td class="c-dist">4.04km away</td><td class="c-time">July 18 at 4:30 am</td><td class="c-status"><span class="badge badge-accepted">Time Accepted</span></td><td class="c-pay"><span class="paid">Payment Made</span></td></tr>
    <tr><td class="c-name">Thomas Crale</td><td class="c-dist">5.7km away</td><td class="c-time"></td><td class="c-status"><span class="badge badge-sent">Request Sent</span></td><td class="c-pay"></td></tr>
    <tr><td class="c-name">Edwin Parlow</td><td class="c-dist">11.13km away</td><td class="c-time"></td><td class="c-status"><span class="badge badge-sent">Request Sent</span></td><td class="c-pay"></td></tr>
    <tr><td class="c-name">Vince Halbrook</td><td class="c-dist">11.91km away</td><td class="c-time"></td><td class="c-status"><span class="badge badge-pending">Pending</span></td><td class="c-pay"></td></tr>
  </tbody>
</table>

<footer class="site-footer">
  <p>Copyrights © Haulvo . 2017 | All rights reserved.</p>
  <span class="code">C11</span>
</footer>
</body>
</html>
```